Business Card Design

We like to use greens as you will see in our logo (but not TOO much green). We are a Dental Clinic in a somewhat eccentric community. We do not like the dated sharp designs which we see many dentists use. We're looking for something bright and fresh while still maintaining the integrity of the profession. Elegance is not necessarily what we are going for... we need for the design to be "mature" but also up-lifting.

See our logo.
Updates

Project Deadline Extended
Reason: We have 5 designs which we like. But we'd like to see a few more before committing to a design.

Project Deadline Extended
Reason: We are awaiting revisions to this project. We are still welcoming designs while we wait to see if designers are able to provide to us the revisions we require in order to proceed with a selection.

Target Market(s)

Younger families - ages late 20's to early 40's

Industry/Entity Type

Business

Contact Information for Business Card

Corwel T. Banfry DDS 2730 W. Halvert Rd. Ste. 7 Royal Oak, MI 48391 (248)555-0174 FX (248)555-0189 info@BrightwellDentalCareMi.com BrigthwellDentalCareMi.com on the back of the card we need an appointment reminder (For____ Date___ Time____) with "If you are unable to keep your appointment, kindly give 48 hours notice" at the bottom. No use of teeth in the design. DOUBLE SIDED DESIGN

Requirements
Should not have
• The use of pictures of teeth

```html
<!DOCTYPE html>
<html lang="en">
<head>
<meta charset="utf-8">
<title>Brightwell Dental Care – Business Card</title>
<link href="https://fonts.googleapis.com/css2?family=Source+Sans+3:wght@400;600;700&family=Tinos:ital,wght@0,400;0,700;1,400&display=swap" rel="stylesheet">
<style>
  :root {
    --bg: #e9e6e1;
    --card: #ffffff;
    --green-dark: #2f7d12;
    --green-brand: #3d8a1a;
    --green-light: #a9dc5a;
    --green-soft: #c9ec9a;
    --ink: #2b2b2b;
    --ink-soft: #444444;
    --rule: #d8d8d8;
  }
  * { box-sizing: border-box; margin: 0; padding: 0; }
  html, body { width: 1200px; height: 492px; overflow: hidden; }
  body {
    background: var(--bg);
    font-family: "Source Sans 3", Arial, sans-serif;
    color: var(--ink);
    position: relative;
  }
  .card {
    position: absolute;
    background: var(--card);
    box-shadow: 0 4px 14px rgba(0,0,0,.18);
  }
  /* Front */
  .card-front { left: 30px; top: 86px; width: 550px; height: 320px; }
  .card-front .tab-left {
    position: absolute; left: -6px; top: 72px; width: 12px; height: 248px;
    background: var(--green-dark); border-radius: 6px 0 0 6px;
  }
  .card-front .tab-right {
    position: absolute; right: -6px; top: 30px; width: 12px; height: 196px;
    background: var(--green-dark); border-radius: 0 6px 6px 0;
  }
  .brand {
    position: absolute; display: flex; align-items: center; gap: 10px;
    color: var(--green-brand); font-weight: 600; line-height: 1.05;
  }
  .brand-dot {
    flex: none; border-radius: 50%; background: var(--green-light);
  }
  .card-front .brand { left: 52px; top: 138px; font-size: 27px; }
  .card-front .brand-dot { width: 34px; height: 34px; }
  .divider {
    position: absolute; left: 283px; top: 40px; width: 1px; height: 240px;
    background: var(--rule);
  }
  .holder {
    position: absolute; left: 304px; top: 54px;
    font-size: 19px; font-weight: 700; color: var(--ink);
  }
  .holder .title { font-size: 14px; font-weight: 600; }
  .contacts {
    position: absolute; left: 304px; top: 92px; list-style: none;
    font-size: 13px; color: var(--ink-soft);
  }
  .contacts li { display: flex; align-items: center; gap: 6px; height: 21px; }
  .contacts svg { width: 12px; height: 12px; flex: none; }
  .address {
    position: absolute; left: 324px; top: 188px;
    font-size: 13px; color: var(--ink-soft); line-height: 1.35; font-style: normal;
  }
  /* Back */
  .card-back { left: 620px; top: 76px; width: 550px; height: 340px; }
  .card-back .brand { left: 30px; top: 84px; font-size: 27px; }
  .card-back .brand-dot { width: 34px; height: 34px; }
  .appointment {
    position: absolute; left: 30px; top: 206px; right: 30px;
    font-size: 14px; color: var(--ink-soft);
  }
  .appointment h2 {
    font-family: "Tinos", "Times New Roman", serif;
    font-weight: 700; font-size: 15px; color: var(--green-dark);
    letter-spacing: .3px; margin-bottom: 8px;
  }
  .field { display: flex; align-items: baseline; gap: 6px; margin-bottom: 10px; }
  .blank { display: inline-block; border-bottom: 1px solid #777; height: 12px; }
  .blank.dotted { border-bottom-style: dotted; }
  .notice {
    position: absolute; left: 30px; bottom: 14px;
    font-family: "Tinos", "Times New Roman", serif; font-style: italic;
    font-size: 14.5px; color: #666;
  }
</style>
</head>
<body>
  <section class="card card-front" aria-label="Business card front">
    <span class="tab-left"></span>
    <span class="tab-right"></span>
    <div class="brand"><span class="brand-dot"></span><span>Brightwell<br>Dental Care</span></div>
    <span class="divider"></span>
    <h1 class="holder">Corwel T. Banfry, <span class="title">DDS</span></h1>
    <ul class="contacts">
      <li><svg viewBox="0 0 12 12"><circle cx="6" cy="6" r="6" fill="#3d8a1a"/><path d="M4 3.2c.4 2.4 1.6 4.2 4 5.4l.8-.9-1.2-.8-.6.5C6.2 6.9 5.4 6 5.2 5.2l.6-.5L5.1 3.4z" fill="#fff"/></svg>(248)555-0174</li>
      <li><svg viewBox="0 0 12 12"><rect x="1" y="4" width="10" height="6" rx="1" fill="#3d8a1a"/><rect x="3" y="1.5" width="6" height="3" fill="#3d8a1a"/><rect x="3" y="6" width="6" height="1.2" fill="#fff"/></svg>(248)555-0189</li>
      <li><svg viewBox="0 0 12 12"><rect x="0.5" y="2.5" width="11" height="7.5" rx="1" fill="#3d8a1a"/><path d="M1 3l5 4 5-4" stroke="#fff" fill="none"/></svg>info@BrightwellDentalCareMi.com</li>
      <li><svg viewBox="0 0 12 12"><circle cx="6" cy="6" r="5.3" fill="#3d8a1a"/><path d="M1 6h10M6 .8c-2.5 3-2.5 7.4 0 10.4M6 .8c2.5 3 2.5 7.4 0 10.4" stroke="#fff" stroke-width=".8" fill="none"/></svg>www.BrigthwellDentalCareMi.com</li>
    </ul>
    <address class="address">2730 W. Halvert Rd. Ste. 7<br>Royal Oak, MI 48391</address>
  </section>

  <section class="card card-back" aria-label="Business card back">
    <div class="brand"><span class="brand-dot"></span><span>Brightwell<br>Dental Care</span></div>
    <div class="appointment">
      <h2>YOUR APPOINTMENT</h2>
      <div class="field">Name : <span class="blank dotted" style="width:290px"></span></div>
      <div class="field">Date : <span class="blank" style="width:95px"></span>
        <span style="margin-left:16px">Time :</span> <span class="blank" style="width:85px"></span> am / pm</div>
    </div>
    <p class="notice">If you are unable to keep your appointment, kindly give 48 hours notice</p>
  </section>
</body>
</html>
```